Export company based in South America (Ecuador) we export flowers, chocolate, and bananas

We need a website that gives our potential clients and introduction into our company and the different types of commodities we export around the world. We are based in Quito, Ecuador so the website should portray the feel of Ecuadorian landscapes within a modern looking website.
At the moment we are exporting roses, chocolate, and bananas so the website should have an intro to our company and then three different areas that describe our three main commodity. The three different sections should explain why each of the products from Ecuador are some of the best in the world in their categories and the benefits of importing the commodity through our company.
Industry/Entity Type
Commodity
Number of Pages Required
4 page

```html
<!DOCTYPE html>
<html lang="en">
<head>
<meta charset="utf-8">
<title>Verandina — Ecuadorian Exports</title>
<link rel="stylesheet" href="https://fonts.googleapis.com/css2?family=Montserrat:wght@400;600;700;800&family=Open+Sans:wght@400;600;700&display=swap">
<style>
:root{
  --green:#2f8a2a;
  --green-dark:#226b1f;
  --green-light:#4da83a;
  --ink:#1e1e1e;
  --text:#555;
  --dark:#171717;
  --white:#fff;
  --line:#9a9a9a;
}
*{box-sizing:border-box;margin:0;padding:0}
html,body{width:1200px;height:3256px;overflow:hidden}
body{font-family:"Open Sans",Arial,sans-serif;color:var(--text);background:var(--white);position:relative}
h1,h2,h3,.brand{font-family:"Montserrat",Arial,sans-serif}
.abs{position:absolute}
.btn{display:inline-block;font:600 15px "Open Sans",sans-serif;padding:10px 26px;background:var(--green);color:var(--white);text-decoration:none}
.btn-outline{background:transparent;border:2px solid var(--white)}

/* header */
.site-header{top:0;left:0;width:1200px;height:88px;background:var(--white)}
.brand{font-weight:800;font-size:46px;color:var(--ink);letter-spacing:-1px}
.site-header .brand{left:88px;top:12px}
.nav{right:88px;top:26px;display:flex;gap:28px;font:600 15px "Open Sans",sans-serif;color:var(--ink);align-items:center}
.nav a{color:var(--ink);text-decoration:none;padding-bottom:6px}
.nav a.active{color:var(--green);border-bottom:3px solid var(--green)}

/* hero */
.hero{top:88px;left:0;width:1200px;height:584px;background:linear-gradient(100deg,#2f4a1f 0%,#4f7a2e 40%,#7a9a4a 65%,#8a3a4a 85%,#5d6a3a 100%)}
.hero-title{left:88px;top:180px;color:var(--white);font-weight:800;font-size:68px;letter-spacing:1px}
.hero-sub{left:88px;top:268px;width:520px;color:var(--white);font:700 20px/1.3 "Open Sans",sans-serif}
.hero .btn{position:absolute;left:88px;top:340px}

/* about */
.about-band{top:672px;left:0;width:1200px;height:330px;background:linear-gradient(180deg,#1b2a30 0%,#2c3e3a 60%,#3d4a2f 100%)}
.about-box{left:88px;top:680px;width:272px;height:320px;background:var(--green);padding:30px 30px}
.about-box h2{color:var(--white);font-weight:800;font-size:44px;line-height:1;margin-bottom:20px}
.about-box p{color:var(--white);font-size:15px;line-height:1.4}
.about-text{left:118px;top:1022px;width:230px;font-size:14px;line-height:1.5}
.about .btn{position:absolute;left:118px;top:1160px}
.card{top:760px;width:240px;height:420px;background:var(--green)}
.card .photo{width:100%;height:340px}
.card span{display:block;color:var(--white);font:700 24px "Open Sans",sans-serif;padding:24px 16px}
.photo-flowers{background:linear-gradient(180deg,#6b86b0 0%,#d8dde6 40%,#8a4a30 75%,#b03020 100%)}
.photo-choc{background:linear-gradient(160deg,#5a3a2a,#a85a4a 45%,#3a2418)}
.photo-banana{background:linear-gradient(180deg,#2f6a1e,#7bb830 55%,#2f5a1a)}

.vline{width:2px;background:var(--line)}

/* chocolate */
.choc-photo{left:128px;top:1300px;width:460px;height:328px;background:linear-gradient(135deg,#2f6a22 0%,#4a8a30 30%,#b0602e 50%,#7a3a20 70%,#3a7a28 100%)}
.section-title{color:var(--green);font-weight:800;font-size:48px}
.title-rule{height:3px;background:var(--green)}
.lead{color:var(--ink);font:700 17px/1.45 "Open Sans",sans-serif}
.body{font-size:15px;line-height:1.55}

/* why */
.why{top:1728px;left:0;width:1200px;height:432px;background:linear-gradient(90deg,var(--green-dark),var(--green) 45%,var(--green-light))}
.why h2{position:absolute;top:40px;width:100%;text-align:center;color:var(--white);font-weight:800;font-size:46px}
.why .intro{position:absolute;left:180px;top:110px;width:840px;text-align:center;color:var(--white);font-size:17px;line-height:1.45}
.features{position:absolute;left:90px;top:225px;width:1020px;display:flex;justify-content:space-between}
.feature{width:240px;text-align:center;color:var(--white)}
.feature svg{width:44px;height:44px;margin-bottom:12px}
.feature h3{font:700 16px "Open Sans",sans-serif;margin-bottom:8px}
.feature p{font-size:13px;line-height:1.4}

/* benefits */
.benefits-photo{left:612px;top:2300px;width:460px;height:438px;background:linear-gradient(160deg,#cfd8e2 0%,#7a96b4 35%,#3a5a80 60%,#b0402a 80%,#5a6a7a 100%)}

/* newsletter & footer */
.footer{top:2812px;left:0;width:1200px;height:444px;background:var(--dark)}
.newsletter{left:88px;top:2732px;width:1024px;height:160px;background:var(--green);padding:36px 30px}
.newsletter h2{color:var(--white);font-weight:800;font-size:36px}
.newsletter p{color:var(--white);font:700 15px/1.4 "Open Sans",sans-serif;width:540px;margin-top:6px}
.sub-form{position:absolute;left:560px;top:56px;display:flex}
.sub-form input{width:380px;height:48px;border:0;padding:0 18px;font:14px "Open Sans",sans-serif}
.sub-form button{width:50px;height:48px;border:0;background:var(--dark);display:flex;align-items:center;justify-content:center}
.footer .brand{position:absolute;left:88px;top:120px;color:var(--white);font-size:50px}
.socials{position:absolute;left:90px;top:200px;display:flex;gap:14px}
.socials i{width:14px;height:14px;border-radius:50%;background:var(--white);display:block}
.footer-about{position:absolute;left:350px;top:132px;width:330px;color:var(--white);font-size:14px;line-height:1.55}
.footer-col{position:absolute;top:128px;color:var(--white)}
.footer-col h3{font:700 24px "Montserrat",sans-serif;margin-bottom:14px}
.footer-col li{list-style:none;font-size:13px;line-height:1.85}
.copyright{position:absolute;left:0;width:100%;top:400px;text-align:center;color:#bbb;font-size:12px}
</style>
</head>
<body>

<header class="site-header abs">
  <div class="brand abs">Verandina</div>
  <nav class="nav abs">
    <a class="active" href="#">Home</a><a href="#">About Us</a><a href="#">Export</a><a href="#">Business</a><a href="#">Gallery</a><a href="#">Contact Us</a>
    <svg width="18" height="18" viewBox="0 0 20 20" aria-label="Search"><circle cx="8" cy="8" r="6" fill="none" stroke="#1e1e1e" stroke-width="2.5"/><line x1="12.5" y1="12.5" x2="18" y2="18" stroke="#1e1e1e" stroke-width="2.5"/></svg>
  </nav>
</header>

<section class="hero abs" role="img" aria-label="Flower farm worker holding freshly cut pink flowers in a greenhouse">
  <h1 class="hero-title abs">VERANDINA</h1>
  <p class="hero-sub abs">Lorem ipsum dolor sit amet, consectetur adipiscing elit, sed do eiusmod</p>
  <a class="btn btn-outline" href="#">Read More</a>
</section>

<section class="about">
  <div class="about-band abs" role="img" aria-label="Andean mountain landscape at dusk"></div>
  <div class="about-box abs">
    <h2>ABOUT<br>US</h2>
    <p>Lorem ipsum dolor sit amet, consectetur adipiscing elit, sed do eiusmod tempor incididunt ut labore et dolore</p>
  </div>
  <p class="about-text abs">Lorem ipsum dolor sit amet, consectetur adipiscing elit, sed do eiusmod tempor incididunt ut labore et dolore magna aliqua.</p>
  <a class="btn" href="#">Read More</a>

  <div class="card abs" style="left:360px"><div class="photo photo-flowers" role="img" aria-label="Snow-capped volcano above a field of red flowers"></div><span>Flowers</span></div>
  <div class="card abs" style="left:610px"><div class="photo photo-choc" role="img" aria-label="Cacao pods and beans"></div><span>Chocolate</span></div>
  <div class="card abs" style="left:860px"><div class="photo photo-banana" role="img" aria-label="Bunch of green bananas on the plant"></div><span>Bananas</span></div>
</section>

<div class="vline abs" style="left:599px;top:1180px;height:120px"></div>

<section class="chocolate">
  <div class="choc-photo abs" role="img" aria-label="Ripe cacao pods on green leaves"></div>
  <h2 class="section-title abs" style="left:700px;top:1288px">CHOCOLATE</h2>
  <div class="title-rule abs" style="left:700px;top:1352px;width:370px"></div>
  <p class="lead abs" style="left:700px;top:1368px;width:380px">Lorem ipsum dolor sit amet, consectetur adipiscing elit, sed do eiusmod tempor labore et dolore magna aliqua.</p>
  <p class="body abs" style="left:700px;top:1450px;width:380px">Lorem ipsum dolor sit amet, consectetur adipiscing elit, sed do eiusmod tempor incididunt ut labore et dolore magna aliqua. Ut enim ad minim veniam, quis nos ullamco laboris nisi ut aliquip ex ea commodo sequat.</p>
  <a class="btn abs" href="#" style="left:700px;top:1584px">Read More</a>
</section>

<div class="vline abs" style="left:599px;top:1660px;height:68px"></div>

<section class="why abs">
  <h2>WHY CHOOSE US</h2>
  <p class="intro">Lorem ipsum dolor sit amet, consectetur adipiscing elit, sed do eiusmod tempor incididunt ut labore et dolore magna aliqua. Ut enim ad minim veniam, quis nostrud exercitation</p>
  <div class="features">
    <div class="feature">
      <svg viewBox="0 0 44 44" fill="none" stroke="#fff" stroke-width="2.5"><rect x="8" y="6" width="28" height="20" rx="2"/><line x1="4" y1="34" x2="40" y2="34"/><line x1="16" y1="26" x2="14" y2="34"/><line x1="28" y1="26" x2="30" y2="34"/></svg>
      <h3>Premium Services</h3><p>Lorem ipsum dolor sit amet,<br>veniam adipiscing elit</p>
    </div>
    <div class="feature">
      <svg viewBox="0 0 44 44" fill="none" stroke="#fff" stroke-width="2.5"><circle cx="22" cy="17" r="11"/><path d="M15 26 12 40 22 35 32 40 29 26"/></svg>
      <h3>Quality</h3><p>Lorem ipsum dolor sit amet,<br>veniam adipiscing elit</p>
    </div>
    <div class="feature">
      <svg viewBox="0 0 44 44" fill="none" stroke="#fff" stroke-width="2.5" stroke-linejoin="round"><rect x="6" y="20" width="8" height="18"/><path d="M14 22 22 8c3 0 4 2 3 6l-2 6h12c2 0 3 2 2 4l-4 12c-1 2-2 2-4 2H14"/></svg>
      <h3>Best Support</h3><p>Lorem ipsum dolor sit amet,<br>veniam adipiscing elit</p>
    </div>
    <div class="feature">
      <svg viewBox="0 0 44 44" fill="none" stroke="#fff" stroke-width="2.5"><circle cx="22" cy="22" r="16"/><path d="M8 16h28M8 28h28M22 6c-6 8-6 24 0 32M22 6c6 8 6 24 0 32"/></svg>
      <h3>Fast Service</h3><p>Lorem ipsum dolor sit amet,<br>veniam adipiscing elit</p>
    </div>
  </div>
</section>

<div class="vline abs" style="left:199px;top:2160px;height:120px"></div>

<section class="benefits">
  <h2 class="section-title abs" style="left:88px;top:2280px">BENEFITS</h2>
  <div class="title-rule abs" style="left:88px;top:2344px;width:330px"></div>
  <p class="lead abs" style="left:88px;top:2360px;width:400px">Lorem ipsum dolor sit amet, consectetur adipiscing elit, sed do eiusmod tempor labore et dolore magna aliqua.</p>
  <p class="body abs" style="left:88px;top:2450px;width:400px">Lorem ipsum dolor sit amet, consectetur adipiscing elit, sed do eiusmod tempor incididunt ut labore et dolore magna aliqua. Ut enim ad minim veniam, quis nos ullamco laboris nisi ut aliquip ex ea commodo sequat.</p>
  <a class="btn abs" href="#" style="left:88px;top:2586px">Read More</a>
  <div class="benefits-photo abs" role="img" aria-label="Port worker with clipboard beside stacked shipping containers"></div>
  <div class="vline abs" style="left:841px;top:2738px;height:0"></div>
</section>

<footer class="footer abs">
  <div class="brand">Verandina</div>
  <div class="socials"><i></i><i></i><i></i><i></i></div>
  <p class="footer-about">Lorem ipsum dolor sit amet, consectetur adipiscing elit, sed do eiusmod tempor incididunt ut labore et dolore magna aliqua.</p>
  <div class="footer-col" style="left:788px">
    <h3>Links</h3>
    <ul><li>Home</li><li>About Us</li><li>Export</li><li>Business</li><li>Gallery</li><li>Contact Us</li></ul>
  </div>
  <div class="footer-col" style="left:980px">
    <h3>Others</h3>
    <ul><li>Faq</li><li>Privacy Policy</li><li>Delivery</li><li>Export</li><li>Terms &amp; Conditions</li></ul>
  </div>
  <p class="copyright">© 2024 The Company name. All Rights Reserved</p>
</footer>

<section class="newsletter abs">
  <h2>SUBSCRIBE NEWSLETTER</h2>
  <p>Lorem ipsum dolor sit amet, consectetur adipiscing elit, sed do ei usmod tempor incididunt ut labore et dolore magna aliqua.</p>
  <form class="sub-form">
    <input type="email" placeholder="Enter Your Email Address">
    <button type="button" aria-label="Subscribe"><svg width="20" height="20" viewBox="0 0 20 20"><path d="M2 10 18 2 13 18 10 11Z" fill="#fff"/></svg></button>
  </form>
</section>

</body>
</html>
```